Bram Keystone Homes needs a business card

We need a business card for a new company in Canada, Ontario. Our company is all about luxury contraction homes for our clients. Our product and services are custom projects design. Under the business logo that will be created, we want a slogan that will be a memorable phrase for consumers to remember us to tell their friends and relatives.

Additional infomation
- Ludovic Entrasse
- President / Ceo
-519.604.3087

Find point what luxury construction products and services can be done

We like to see colors:
- #663300
- and something other colors or color that would attract the client needs and wants

The final design should communicate leads from new or old clients that will grow our empire. Most of all, we try to work among the budget that clients want

NOTE
- we also need an icon for the business (Example: Instagram, Facebook, and Whatsapp icons)
- We want the company name to be remembered easily for clients and our distributors who would get our orders.
- we need an icon on the business cards: Facebook and Instagram.

Thanks,
Bram Keystone Homes

```html
<!DOCTYPE html>
<html lang="en">
<head>
<meta charset="utf-8">
<title>Bram Keystone Homes – Business Card</title>
<link rel="stylesheet" href="https://fonts.googleapis.com/css2?family=Ubuntu:wght@300;400;700&display=swap">
<style>
  :root {
    --brown: #663300;
    --black: #000000;
    --white: #ffffff;
    --shadow: rgba(0, 0, 0, 0.28);
  }
  * { box-sizing: border-box; margin: 0; padding: 0; }
  html, body {
    width: 1200px;
    height: 1200px;
    overflow: hidden;
    background: var(--white);
    font-family: "Ubuntu", sans-serif;
  }
  .canvas { position: relative; width: 1200px; height: 1200px; }

  .card { position: absolute; overflow: hidden; }
  .card-front { left: 164px; top: 92px; width: 863px; height: 484px; background: var(--black); }
  .card-back {
    left: 174px; top: 636px; width: 863px; height: 550px; background: var(--white);
    box-shadow: -10px -10px 12px -6px var(--shadow), 8px 0 10px -6px var(--shadow);
  }
  .base-band { position: absolute; left: 0; right: 0; bottom: 0; height: 31px; background: var(--brown); }

  .brand-mark { position: absolute; display: flex; align-items: center; gap: 10px; }
  .brand-mark .mark-square { width: 46px; height: 46px; background: var(--brown); flex: none; }
  .brand-mark .mark-name { color: var(--brown); font-weight: 700; font-size: 17px; line-height: 1.1; width: 86px; }
  .card-front .brand-mark { left: 16px; top: 30px; }
  .card-back .brand-mark { right: 10px; top: 22px; flex-direction: row-reverse; text-align: right; }

  .company-name { color: var(--brown); font-weight: 700; white-space: nowrap; }
  .tagline { color: var(--brown); font-weight: 400; text-transform: uppercase; white-space: nowrap; }

  .front-title { position: absolute; left: 0; right: 0; top: 210px; text-align: center; }
  .front-title .company-name { font-size: 54px; letter-spacing: 0.5px; line-height: 1; }
  .front-title .tagline { font-size: 19px; margin-top: 14px; }

  .back-title { position: absolute; left: 10px; top: 8px; }
  .back-title .company-name { font-size: 35px; line-height: 1.1; letter-spacing: 0.3px; }
  .back-title .tagline { font-size: 14px; margin-left: 9px; }

  .contact { position: absolute; left: 0; width: 812px; top: 218px; text-align: center; color: var(--brown); }
  .contact .person-name { font-weight: 700; font-size: 35px; line-height: 1.1; letter-spacing: 0.3px; }
  .contact .person-role { font-weight: 300; font-size: 36px; line-height: 1.1; }
  .contact .phone { font-weight: 300; font-size: 35px; margin-top: 28px; letter-spacing: 1px; }
</style>
</head>
<body>
<main class="canvas">
  <section class="card card-front">
    <div class="brand-mark">
      <span class="mark-square"></span>
      <span class="mark-name">Bram Keystone Homes</span>
    </div>
    <div class="front-title">
      <h1 class="company-name">Bram Keystone Homes</h1>
      <p class="tagline">- Home Renovations - Custom Project Design -</p>
    </div>
    <div class="base-band"></div>
  </section>

  <section class="card card-back">
    <div class="back-title">
      <h2 class="company-name">Bram Keystone Homes</h2>
      <p class="tagline">- Home Renovations - Custom Project Design -</p>
    </div>
    <div class="brand-mark">
      <span class="mark-square"></span>
      <span class="mark-name">Bram Keystone Homes</span>
    </div>
    <div class="contact">
      <p class="person-name">Ludovic Entrasse</p>
      <p class="person-role">CEO</p>
      <p class="phone">519.604.3087</p>
    </div>
    <div class="base-band"></div>
  </section>
</main>
</body>
</html>
```